I am looking for a modern, clean and neat design for a reflexology and well being business. The business name is Gralo Tund (this is an old Latin word for wellbeing). The colours I would like are purple, white and grey. I am open to suggestions for pictures such as healing or working hands, a pair of feet, images that represent my business that you may think of....... or maybe you think no images at all would be best? My tag line is: "Relax, Renew, Revive" or "Find you balance......... Relax, Renew, Revive" I can decide which I want so I would like to see what both would look like. I would like space on the back to write the client's appointment date and time (more than once)

```html
<!DOCTYPE html>
<html lang="en">
<head>
<meta charset="utf-8">
<title>Gralo Tund – Business Card</title>
<link rel="stylesheet" href="https://fonts.googleapis.com/css2?family=Open+Sans:wght@400;600;700&display=swap">
<style>
  :root {
    --stage: #151515;
    --card-front: #f3f3f3;
    --card-back: #eeedee;
    --ink: #3c3c3c;
    --ink-soft: #444444;
    --purple: #9a10b2;
    --card-edge: #d8d8d8;
  }
  html, body {
    margin: 0;
    padding: 0;
    width: 1200px;
    height: 900px;
    overflow: hidden;
    background: var(--stage);
  }
  .canvas {
    position: relative;
    width: 1200px;
    height: 900px;
    font-family: "Open Sans", Arial, sans-serif;
    color: var(--ink);
  }
  .card {
    position: absolute;
    top: 184px;
    width: 301px;
    height: 490px;
    border-radius: 12px;
    border: 1px solid var(--card-edge);
    box-sizing: border-box;
  }
  .card--front { left: 299px; background: var(--card-front); }
  .card--back  { left: 645px; width: 304px; background: var(--card-back); }

  .brand-name {
    position: absolute;
    left: 0;
    right: 0;
    top: 132px;
    margin: 0;
    text-align: center;
    font-size: 44px;
    font-weight: 600;
    line-height: 1;
    color: var(--ink);
    letter-spacing: 0.5px;
  }
  .card--back .brand-name { top: 118px; }

  .tagline {
    position: absolute;
    left: 0; right: 0;
    top: 190px;
    margin: 0;
    text-align: center;
    font-size: 14px;
    font-weight: 600;
    line-height: 18px;
    color: var(--purple);
    letter-spacing: 1px;
  }
  .card--back .tagline { top: 172px; }

  .person {
    position: absolute;
    left: 0; right: 0;
    top: 268px;
    text-align: center;
  }
  .person__name {
    margin: 0;
    font-size: 19px;
    font-weight: 600;
    line-height: 24px;
    color: var(--ink);
  }
  .person__name .accent { color: var(--purple); }
  .person__role {
    margin: 0;
    font-size: 14px;
    line-height: 20px;
    color: var(--ink-soft);
  }

  .contact {
    position: absolute;
    left: 0; right: 0;
    top: 341px;
    margin: 0;
    padding: 0;
    list-style: none;
    text-align: center;
    font-size: 14px;
    line-height: 20px;
    color: var(--ink-soft);
  }
  .contact__icon {
    display: inline-block;
    vertical-align: middle;
    margin-right: 8px;
    margin-top: -3px;
  }

  .address {
    position: absolute;
    left: 0; right: 0;
    top: 419px;
    margin: 0;
    text-align: center;
    font-style: normal;
    font-size: 14px;
    line-height: 17px;
    color: var(--ink-soft);
  }

  .appointment__title {
    position: absolute;
    left: 19px;
    top: 222px;
    margin: 0;
    font-size: 16.5px;
    font-weight: 600;
    color: var(--ink);
    white-space: nowrap;
  }
  .appointment__title .accent { color: var(--purple); }

  .field-row {
    position: absolute;
    left: 59px;
    margin: 0;
    font-size: 14.5px;
    font-weight: 700;
    line-height: 20px;
    color: var(--purple);
    white-space: nowrap;
  }
  .field-row--name { top: 272px; }
  .field-row--slot-1 { top: 310px; }
  .field-row--slot-2 { top: 344px; }
  .field-row--slot-3 { top: 378px; }
  .field-row__dots {
    font-weight: 400;
    color: var(--ink);
    letter-spacing: 0.5px;
    font-size: 13px;
  }
  .field-row__gap { display: inline-block; width: 10px; }

  .notice {
    position: absolute;
    left: 0; right: 0;
    top: 427px;
    margin: 0;
    text-align: center;
    font-size: 14.5px;
    font-weight: 700;
    line-height: 19px;
    color: var(--purple);
    text-transform: uppercase;
  }
</style>
</head>
<body>
<main class="canvas">

  <section class="card card--front" aria-label="Business card front">
    <p class="brand-name">Gralo Tund</p>
    <p class="tagline">Relax, Renew, Revive</p>

    <div class="person">
      <p class="person__name">MARA <span class="accent">VELL</span></p>
      <p class="person__role">Managing Director</p>
    </div>

    <ul class="contact">
      <li>
        <svg class="contact__icon" width="10" height="8" viewBox="0 0 10 8" aria-hidden="true">
          <path d="M0 2.6 Q5 -1 10 2.6 L8.6 3.8 L7 2.4 L3 2.4 L1.4 3.8 Z" fill="var(--purple)"/>
          <rect x="2" y="3.4" width="6" height="4.4" rx="1" fill="var(--purple)"/>
        </svg>555-014-2270
      </li>
      <li>
        <svg class="contact__icon" width="10" height="8" viewBox="0 0 10 8" aria-hidden="true">
          <rect x="0" y="0.5" width="10" height="7" fill="var(--purple)"/>
          <path d="M0.5 1 L5 4.6 L9.5 1" stroke="var(--card-front)" stroke-width="1" fill="none"/>
        </svg>hello@gralotund.com
      </li>
    </ul>

    <address class="address">48, Linden Court Lane<br>Northvale, 204518</address>
  </section>

  <section class="card card--back" aria-label="Business card back, appointment reminder">
    <p class="brand-name">Gralo Tund</p>
    <p class="tagline">Relax, Renew, Revive</p>

    <h2 class="appointment__title">YOUR NEXT <span class="accent">APPOINTMENT ON</span></h2>

    <p class="field-row field-row--name">NAME : <span class="field-row__dots">...............................</span></p>
    <p class="field-row field-row--slot-1">DATE : <span class="field-row__dots">...........</span><span class="field-row__gap"></span>TIME : <span class="field-row__dots">............</span></p>
    <p class="field-row field-row--slot-2">DATE : <span class="field-row__dots">...........</span><span class="field-row__gap"></span>TIME : <span class="field-row__dots">............</span></p>
    <p class="field-row field-row--slot-3">DATE : <span class="field-row__dots">...........</span><span class="field-row__gap"></span>TIME : <span class="field-row__dots">............</span></p>

    <p class="notice">If unable to keep appointment,<br>kindly give 24hrs notice.</p>
  </section>

</main>
</body>
</html>
```